Verlindo Magician

I want the business card for my business to give to people who watch that later I will be employed to show magic here is my website http://www.balsamomagicien.com/I want the interesting design , i am very opened for formal and informal, I watch a lot of design so don't stick to the common shape and form but i hope it can also be produced the thing to write on will be the same as in picture that i will upload , i also will upload the logo for you that so can be easy to useDenis CostilleMagicianMAGICIAN BALSAMO 17 rue des Tilleuls - 48210 VALMORENCE contact@verlindoillusions.example tel. 0381 946 157 tel. 0674 219 503

```html
<!DOCTYPE html>
<html lang="en">
<head>
<meta charset="utf-8">
<title>Verlindo Magician – Business Card</title>
<link rel="stylesheet" href="https://fonts.googleapis.com/css2?family=Montserrat:wght@700&family=Poppins:wght@300;400&display=swap">
<style>
  :root {
    --backdrop: #e9e6e1;
    --card: #ffffff;
    --ink: #1a1a1a;
    --text: #333333;
    --accent: #e3202a;
    --rule: #222222;
    --pattern-a: #f7f4f4;
    --pattern-b: #fbeeee;
  }
  * { box-sizing: border-box; margin: 0; padding: 0; }
  html, body { width: 1200px; height: 768px; overflow: hidden; }
  body {
    background: var(--backdrop);
    display: flex;
    align-items: center;
    justify-content: center;
    gap: 70px;
    font-family: "Poppins", sans-serif;
  }
  .card {
    width: 400px;
    height: 640px;
    background: var(--card);
    border-radius: 26px;
    box-shadow: 0 10px 30px rgba(0,0,0,.18);
    position: relative;
    overflow: hidden;
  }
  .portrait {
    width: 270px; height: 220px;
    background: radial-gradient(ellipse 60% 55% at 50% 58%, rgba(26,26,26,1) 0%, rgba(40,40,40,.95) 55%, rgba(40,40,40,0) 100%);
  }
  /* Front */
  .card-front { display: flex; flex-direction: column; align-items: center; padding-top: 70px; }
  .name {
    margin-top: 26px;
    font-family: "Montserrat", sans-serif;
    font-weight: 700;
    font-size: 25px;
    letter-spacing: 1.5px;
    color: var(--ink);
    text-transform: uppercase;
  }
  .role { color: var(--accent); font-size: 17px; letter-spacing: 1px; margin-top: -2px; }
  .divider { width: 160px; display: flex; align-items: center; gap: 8px; margin: 16px 0 12px; }
  .divider-wide { width: 180px; }
  .divider::before, .divider::after { content: ""; flex: 1; height: 1px; background: var(--rule); }
  .icon { width: 20px; height: 20px; flex: none; }
  .details { text-align: center; color: var(--text); font-size: 14px; line-height: 1.55; letter-spacing: .6px; }
  .company { text-transform: uppercase; }
  /* Back */
  .card-back {
    background:
      radial-gradient(circle at 50% 50%, rgba(255,255,255,.85) 0%, rgba(255,255,255,0) 70%),
      linear-gradient(135deg, var(--pattern-a), var(--pattern-b));
    display: flex; flex-direction: column; align-items: center; justify-content: center;
  }
  .back-pattern { position: absolute; inset: 0; }
  .portrait-back { position: relative; }
  .brand {
    position: relative;
    margin-top: 18px;
    font-weight: 300;
    font-size: 40px;
    letter-spacing: 3px;
    color: var(--ink);
    text-align: center;
    line-height: 1;
  }
  .brand-sub {
    position: relative;
    font-weight: 300;
    font-size: 13px;
    letter-spacing: 2px;
    color: var(--ink);
    margin-top: 6px;
    display: flex; align-items: center; gap: 6px;
  }
  .brand-sub::before { content: ""; width: 7px; height: 7px; border-radius: 50%; background: var(--accent); }
</style>
</head>
<body>
  <article class="card card-front">
    <div class="portrait" role="img" aria-label="Black and white illustration of the magician holding a playing card"></div>
    <h1 class="name">Marc Ravoulet</h1>
    <p class="role">Magician</p>

    <div class="divider">
      <svg class="icon" viewBox="0 0 20 20" aria-hidden="true"><circle cx="10" cy="10" r="10" fill="var(--ink)"/><path d="M10 4a3.5 3.5 0 0 0-3.5 3.5C6.5 10 10 15 10 15s3.5-5 3.5-7.5A3.5 3.5 0 0 0 10 4z" fill="var(--accent)"/><circle cx="10" cy="7.5" r="1.3" fill="var(--ink)"/></svg>
    </div>
    <div class="details">
      <p class="company">Magician Verlindo</p>
      <p>17 rue des Tilleuls - 48210 VALMORENCE</p>
    </div>

    <div class="divider divider-wide">
      <svg class="icon" viewBox="0 0 20 20" aria-hidden="true"><circle cx="10" cy="10" r="10" fill="var(--ink)"/><path d="M7 5l2 2.5-1.2 1.3a7 7 0 0 0 3.4 3.4l1.3-1.2L15 13l-1.2 1.6C9.5 14.5 5.5 10.5 5.4 6.2z" fill="var(--accent)"/></svg>
      <svg class="icon" viewBox="0 0 20 20" aria-hidden="true"><circle cx="10" cy="10" r="10" fill="var(--ink)"/><rect x="5" y="6.5" width="10" height="7" rx="1" fill="var(--accent)"/><path d="M5 7l5 3.5L15 7" stroke="var(--ink)" stroke-width="1" fill="none"/></svg>
      <svg class="icon" viewBox="0 0 20 20" aria-hidden="true"><circle cx="10" cy="10" r="10" fill="var(--ink)"/><circle cx="10" cy="10" r="5" fill="none" stroke="var(--accent)" stroke-width="1.4"/><path d="M5 10h10M10 5c-2.5 3-2.5 7 0 10M10 5c2.5 3 2.5 7 0 10" stroke="var(--accent)" stroke-width="1.1" fill="none"/></svg>
    </div>
    <div class="details">
      <p>0381 946 157 | 0674 219 503</p>
      <p>contact@verlindoillusions.example</p>
      <p>www.verlindoillusions.example</p>
    </div>
  </article>

  <article class="card card-back">
    <div class="back-pattern" role="img" aria-label="Faint pattern of playing card suits"></div>
    <div class="portrait portrait-back" role="img" aria-label="Black and white illustration of the magician holding a playing card"></div>
    <p class="brand">VERLINDO</p>
    <p class="brand-sub">MAGICIEN</p>
  </article>
</body>
</html>
```